Quellmar Capital LLC

Need Professional Business cards for New Investment Fund

Target Market(s)

High Quality investors

Industry/Entity Type

Financial

Contact Information for Business Card

Phone Number +1 555 284 6190
Name Lukas Varenko
Title Fund Manager
email lv@FundQuellmar.com
Website www.FundQuellmar.com

Colors

Designer to choose colors to be used in the design.

Requirements
Must have
• Must have our Logo and all of the above. Must be made so lettering and loge can be raised

```html
<!DOCTYPE html>
<html lang="en">
<head>
<meta charset="utf-8">
<title>Quellmar Capital LLC — Business Card</title>
<link href="https://fonts.googleapis.com/css2?family=Jost:wght@400;500;600&display=swap" rel="stylesheet">
<style>
  :root {
    --backdrop: #999999;
    --paper: #f4f4f2;
    --ink-black: #0c0c0c;
    --brand-green: #43b843;
    --edge-green: #2fa52f;
    --text-grey: #6f6f6f;
  }
  * { box-sizing: border-box; margin: 0; padding: 0; }
  html, body {
    width: 1200px; height: 943px; overflow: hidden;
    background: var(--backdrop);
    font-family: "Jost", "Century Gothic", sans-serif;
  }
  .canvas { position: relative; width: 1200px; height: 943px; }
  .card {
    position: absolute;
    width: 560px; height: 320px;
    border-bottom: 4px solid var(--edge-green);
    border-radius: 2px;
  }
  .card--front { left: 290px; top: 110px; background: var(--paper); }
  .card--back  { left: 350px; top: 513px; background: var(--ink-black); }

  .wordmark {
    position: absolute; display: flex; align-items: center; gap: 8px;
    font-weight: 500; letter-spacing: 3px; text-transform: uppercase;
    white-space: nowrap; color: var(--brand-green);
  }
  .wordmark__square { width: 10px; height: 10px; background: var(--brand-green); flex: none; }
  .card--front .wordmark { left: 40px; top: 40px; font-size: 22px; }
  .card--back .wordmark {
    left: 50%; top: 50%; transform: translate(-50%, -50%);
    font-size: 40px;
  }
  .card--back .wordmark__square { width: 16px; height: 16px; }

  .holder { position: absolute; left: 40px; top: 170px; }
  .holder__name {
    font-size: 21px; font-weight: 600; letter-spacing: 1.5px;
    color: var(--brand-green); text-transform: uppercase; white-space: nowrap;
  }
  .holder__title { font-size: 15px; color: var(--text-grey); letter-spacing: 1px; }

  .contacts { position: absolute; left: 40px; top: 236px; list-style: none; }
  .contacts li {
    display: flex; align-items: center; gap: 10px; white-space: nowrap;
    font-size: 14px; color: var(--text-grey); letter-spacing: 1px; line-height: 22px;
  }
  .contacts svg { width: 12px; height: 12px; flex: none; }
</style>
</head>
<body>
<main class="canvas">
  <section class="card card--front" aria-label="Card front">
    <div class="wordmark"><span class="wordmark__square"></span>Quellmar</div>
    <div class="holder">
      <p class="holder__name">Lukas Varenko</p>
      <p class="holder__title">Fund Manager</p>
    </div>
    <ul class="contacts">
      <li>
        <svg viewBox="0 0 12 12" aria-hidden="true"><path d="M2.5 1 L4.5 1 L5 3.5 L3.8 4.5 Q5 7 7.5 8.2 L8.5 7 L11 7.5 L11 9.5 Q10.5 11 9 11 Q2 10 1 3 Q1 1.5 2.5 1Z" fill="var(--brand-green)"/></svg>
        +1 555 284 6190
      </li>
      <li>
        <svg viewBox="0 0 12 12" aria-hidden="true"><rect x="1" y="2.5" width="10" height="7" fill="none" stroke="var(--brand-green)" stroke-width="1.2"/><path d="M1 2.5 L6 6.5 L11 2.5" fill="none" stroke="var(--brand-green)" stroke-width="1.2"/></svg>
        lv@FundQuellmar.com
      </li>
      <li>
        <svg viewBox="0 0 12 12" aria-hidden="true"><circle cx="6" cy="6" r="5" fill="none" stroke="var(--brand-green)" stroke-width="1.1"/><ellipse cx="6" cy="6" rx="2.2" ry="5" fill="none" stroke="var(--brand-green)" stroke-width="1"/><path d="M1 6 H11" stroke="var(--brand-green)" stroke-width="1"/></svg>
        www.FundQuellmar.com
      </li>
    </ul>
  </section>

  <section class="card card--back" aria-label="Card back">
    <div class="wordmark"><span class="wordmark__square"></span>Quellmar</div>
  </section>
</main>
</body>
</html>
```